Bookkeeping business needs a digital and print flyer

We need a flyer to promote our virtual bookkeeping services to small and mid-sized businesses in the United States. We want the content and design of the flyer to be consistent with our website: www.brightlanebookkeeping.example. We would like both a print version and a digital version of the flyer.

```html
<!DOCTYPE html>
<html lang="en">
<head>
<meta charset="utf-8">
<title>Bright Lane Bookkeeping – Flyer</title>
<link href="https://fonts.googleapis.com/css2?family=Montserrat:wght@300&family=Poppins:ital,wght@0,400;0,600;0,700;0,800;1,700&display=swap" rel="stylesheet">
<style>
  :root {
    --navy: #2b2d52;
    --navy-deep: #12143f;
    --gold: #f2c12e;
    --gold-pale: #f9e3a0;
    --paper: #ececee;
    --card: #f4f4f6;
    --ink: #111111;
    --bullet: #2d3a8c;
    --stage: #c9d3d3;
  }
  * { box-sizing: border-box; margin: 0; padding: 0; }
  html, body { width: 1200px; height: 1117px; overflow: hidden; }
  body {
    background: var(--stage);
    font-family: "Poppins", sans-serif;
    color: var(--ink);
    position: relative;
  }
  .flyer {
    position: absolute;
    left: 220px; top: 20px;
    width: 760px; height: 1077px;
    background: var(--paper);
    overflow: hidden;
  }
  .hero {
    position: absolute; left: 0; top: 0;
    width: 760px; height: 345px;
    background: linear-gradient(135deg, #34365c 0%, var(--navy) 55%, #25274a 100%);
  }
  .brand-name {
    position: absolute; top: 62px; left: 0; width: 760px;
    text-align: center;
    font-family: "Montserrat", sans-serif; font-weight: 300;
    font-size: 30px; letter-spacing: 2px; color: #ffffff; line-height: 1;
  }
  .headline {
    position: absolute; top: 155px; left: 0; width: 760px;
    text-align: center; color: #ffffff;
    font-weight: 700; font-size: 39px; line-height: 1.13;
  }
  .tagline {
    position: absolute; top: 250px; left: 0; width: 760px;
    text-align: center; color: var(--gold);
    font-weight: 600; font-size: 17px;
  }
  .photo {
    position: absolute; left: 404px; top: 290px;
    width: 290px; height: 177px;
    border: 5px solid #ffffff; border-radius: 18px;
    background: linear-gradient(135deg, #8a6a45 0%, #3c5560 45%, #1d3a4c 100%);
  }
  .intro {
    position: absolute; left: 55px; top: 368px; width: 330px;
    text-align: center; font-weight: 800; font-size: 22px; line-height: 1.2;
  }
  .benefits {
    position: absolute; left: 55px; top: 465px;
    width: 317px; height: 395px;
    background: var(--card); border-radius: 20px;
    box-shadow: 0 2px 8px rgba(0,0,0,0.08);
    padding: 16px 16px 0 20px;
  }
  .benefits h2 {
    text-align: center; font-size: 18px; font-weight: 700; line-height: 1.15;
    padding-bottom: 10px; margin: 0 8px 14px 0;
    border-bottom: 2px solid var(--gold);
  }
  .benefit { display: flex; gap: 11px; font-size: 14.2px; line-height: 1.16; margin-bottom: 8px; }
  .benefit svg { flex: none; margin-top: 3px; }
  .benefit em { display: block; font-weight: 700; font-style: italic; }
  .services { position: absolute; left: 406px; top: 483px; width: 280px; }
  .services h2 {
    font-size: 18.5px; font-weight: 700; line-height: 1.2;
    padding-bottom: 6px; margin-bottom: 11px;
    border-bottom: 2px solid var(--gold); width: 165px; white-space: nowrap;
  }
  .services ul { list-style: none; }
  .services li {
    position: relative; padding-left: 18px;
    font-size: 13.2px; line-height: 1.17; margin-bottom: 8px;
  }
  .services li::before {
    content: ""; position: absolute; left: 2px; top: 6px;
    width: 4px; height: 4px; border-radius: 50%; background: var(--bullet);
  }
  .cta-band {
    position: absolute; left: 0; top: 872px; width: 760px; height: 124px;
    background: linear-gradient(180deg, var(--gold-pale) 0%, var(--gold) 45%, var(--gold) 100%);
  }
  .cta {
    position: absolute; left: 0; top: 948px; width: 760px;
    text-align: center; font-weight: 800; font-size: 24.5px;
  }
  .contact {
    position: absolute; left: 0; top: 996px; width: 760px; height: 81px;
    background: var(--navy-deep);
    display: flex; justify-content: center; align-items: center; gap: 16px;
    color: #ffffff; font-weight: 600; font-size: 13.2px;
  }
  .contact span { display: flex; align-items: center; gap: 5px; }
</style>
</head>
<body>
  <main class="flyer">
    <header class="hero">
      <p class="brand-name">BRIGHT LANE BOOKKEEPING</p>
      <h1 class="headline">Virtual Bookkeeping for Small<br>and mid-sized businesses</h1>
      <p class="tagline">Build Your Business by Focusing on What You Love</p>
    </header>

    <div class="photo" role="img" aria-label="Photo of hands typing on a laptop with floating digital document icons"></div>

    <p class="intro">Say Hello to a reliable, hassle-free bookkeeping solution!</p>

    <section class="benefits">
      <h2>What you get with Bright Lane Bookkeeping</h2>
      <div class="benefit">
        <svg width="12" height="12" viewBox="0 0 12 12"><circle cx="6" cy="6" r="6" fill="#f2c12e"/><path d="M3.3 6.2l1.8 1.8 3.6-3.6" stroke="#fff" stroke-width="1.5" fill="none"/></svg>
        <p>Worry no more about finding time and energy to tackle bookkeeping <em>– Hakuna Matata!</em></p>
      </div>
      <div class="benefit">
        <svg width="12" height="12" viewBox="0 0 12 12"><circle cx="6" cy="6" r="6" fill="#f2c12e"/><path d="M3.3 6.2l1.8 1.8 3.6-3.6" stroke="#fff" stroke-width="1.5" fill="none"/></svg>
        <p>Keep more of your hard-earned money by maximizing tax deductions <em>– Ka-Ching!</em></p>
      </div>
      <div class="benefit">
        <svg width="12" height="12" viewBox="0 0 12 12"><circle cx="6" cy="6" r="6" fill="#f2c12e"/><path d="M3.3 6.2l1.8 1.8 3.6-3.6" stroke="#fff" stroke-width="1.5" fill="none"/></svg>
        <p>Understand those confusing financial reports to take your business to the next level <em>– Booyah!</em></p>
      </div>
      <div class="benefit">
        <svg width="12" height="12" viewBox="0 0 12 12"><circle cx="6" cy="6" r="6" fill="#f2c12e"/><path d="M3.3 6.2l1.8 1.8 3.6-3.6" stroke="#fff" stroke-width="1.5" fill="none"/></svg>
        <p>Celebrate each month’s wins during monthly consultations <em>–Hooray!</em></p>
      </div>
      <div class="benefit">
        <svg width="12" height="12" viewBox="0 0 12 12"><circle cx="6" cy="6" r="6" fill="#f2c12e"/><path d="M3.3 6.2l1.8 1.8 3.6-3.6" stroke="#fff" stroke-width="1.5" fill="none"/></svg>
        <p>Stress-free tax time <em>– Oh Yeah!</em></p>
      </div>
    </section>

    <section class="services">
      <h2>Bookkeeping Tailored to YOUR<br>Business Needs</h2>
      <ul>
        <li>Catch-up and clean-up services</li>
        <li>Transaction importation and categorization</li>
        <li>Monthly reconciliation of all accounts, including assets and loans.</li>
        <li>Monthly financial reports (Balance Sheet, Income Statement, Cash Flow)</li>
        <li>Monthly video conference</li>
        <li>Annual tax-prep package sent to your preparer</li>
        <li>A/R &amp; A/P</li>
        <li>Payroll coordination</li>
        <li>1099s</li>
        <li>Bill pay and receipt management</li>
        <li>Budgeting</li>
      </ul>
    </section>

    <div class="cta-band" role="img" aria-label="Decorative layered yellow wave band"></div>
    <p class="cta">Take bookkeeping off your 'To Do List' for good!</p>

    <footer class="contact">
      <span>
        <svg width="13" height="13" viewBox="0 0 14 14"><circle cx="7" cy="7" r="7" fill="#f2c12e"/><path d="M4.6 3.6l1.4 1.7-.8.9c.5 1 1.4 1.9 2.4 2.4l.9-.8 1.7 1.4-.9 1.1C6.9 10 4 7.1 3.5 4.5z" fill="#12143f"/></svg>
        555-014-2297
      </span>
      <span>
        <svg width="13" height="13" viewBox="0 0 14 14"><circle cx="7" cy="7" r="7" fill="#f2c12e"/><rect x="3.8" y="4.6" width="6.4" height="4.8" fill="none" stroke="#12143f" stroke-width="1"/><path d="M3.8 4.6L7 7.3l3.2-2.7" fill="none" stroke="#12143f" stroke-width="1"/></svg>
        dana@brightlanebookkeeping.example
      </span>
      <span>
        <svg width="13" height="13" viewBox="0 0 14 14"><circle cx="7" cy="7" r="7" fill="#f2c12e"/><circle cx="7" cy="7" r="3.6" fill="none" stroke="#12143f" stroke-width="1"/><path d="M3.4 7h7.2M7 3.4c-1.6 2.2-1.6 5 0 7.2M7 3.4c1.6 2.2 1.6 5 0 7.2" fill="none" stroke="#12143f" stroke-width="0.9"/></svg>
        brightlanebookkeeping.example
      </span>
    </footer>
  </main>
</body>
</html>
```